Volbrey Inc Business Card

Looking to get an updated business card for a Contract Machining company (www.volbreyinc.example) - looking for a clean design the portrays the technical nature of the business - colors can follow the website design and be in any combination that makes sense (red black, white, metallic or silver) - logos attached for use also. Would like space for: Name, title, business phone (555 214-3086), cell phone , website (www.volbreyinc.example) - possibly QR code could be integrated for website (designer choice), business address - 418 Harlow Bend, Alderwick, MN 48199 (cards will be for 4 employees, I will either need to modify a template or I can provide individual information)
Target Market(s)
Aerospace, defense and medical device manufacturing companies that need machining
Industry/Entity Type
Machining for aerospace, defense, medical
Contact Information for Business Card
Name, Title, Business Phone, Cell Phone, email, business website and business address
Look and feel

```html
<!DOCTYPE html>
<html lang="en">
<head>
<meta charset="utf-8">
<title>Volbrey Inc Business Card</title>
<link href="https://fonts.googleapis.com/css2?family=Montserrat:wght@400;500;800&display=swap" rel="stylesheet">
<style>
  :root {
    --stage: #e6e7e9;
    --card-dark: #111316;
    --card-light: #ffffff;
    --silver: #c3c6ca;
    --red: #b52025;
    --ink: #141414;
    --rule: #b8b8b8;
    --white: #ffffff;
  }
  * { margin: 0; padding: 0; box-sizing: border-box; }
  html, body { width: 1200px; height: 895px; overflow: hidden; }
  body {
    background: var(--stage);
    font-family: "Montserrat", Arial, sans-serif;
    display: flex;
    flex-direction: column;
    align-items: center;
    justify-content: center;
    gap: 40px;
  }
  .card {
    width: 640px;
    height: 366px;
    border-radius: 22px;
    position: relative;
    box-shadow: 0 10px 24px rgba(0,0,0,0.18);
    overflow: hidden;
  }

  /* Back side */
  .card-back {
    background: var(--card-dark);
    display: flex;
    flex-direction: column;
    align-items: center;
    justify-content: center;
  }
  .back-mark {
    width: 108px;
    height: 108px;
    border-radius: 50%;
    background: var(--silver);
    margin-bottom: 22px;
  }
  .back-name {
    color: var(--silver);
    font-weight: 800;
    font-size: 34px;
    letter-spacing: 1px;
    line-height: 1;
    white-space: nowrap;
  }
  .back-web {
    color: var(--white);
    font-weight: 500;
    font-size: 15px;
    letter-spacing: 0.5px;
    margin-top: 34px;
  }

  /* Front side */
  .card-front {
    background: var(--card-light);
    display: flex;
    align-items: center;
  }
  .brand {
    width: 350px;
    display: flex;
    align-items: center;
    gap: 14px;
    padding-left: 34px;
  }
  .brand-mark {
    width: 62px;
    height: 62px;
    border-radius: 50%;
    background: var(--red);
    flex-shrink: 0;
  }
  .brand-name {
    color: var(--ink);
    font-weight: 800;
    font-size: 27px;
    line-height: 1;
    white-space: nowrap;
  }
  .divider {
    width: 1px;
    height: 170px;
    background: var(--rule);
    margin-right: 24px;
    flex-shrink: 0;
  }
  .details { color: var(--ink); font-size: 13.5px; line-height: 1.35; white-space: nowrap; }
  .person-name {
    color: var(--red);
    font-weight: 800;
    font-size: 20px;
    text-transform: uppercase;
    line-height: 1.1;
  }
  .person-title { font-size: 14px; margin-bottom: 10px; }
  .address { margin-bottom: 10px; }
  .contact-list { list-style: none; }
  .contact-list li { display: flex; align-items: center; gap: 8px; }
  .contact-list svg { width: 12px; height: 12px; fill: var(--red); flex-shrink: 0; }
</style>
</head>
<body>

  <section class="card card-back">
    <div class="back-mark"></div>
    <div class="back-name">VOLBREY INC.</div>
    <div class="back-web">www.volbreyinc.example</div>
  </section>

  <section class="card card-front">
    <div class="brand">
      <div class="brand-mark"></div>
      <div class="brand-name">VOLBREY INC.</div>
    </div>
    <div class="divider"></div>
    <div class="details">
      <div class="person-name">Dane Corwell</div>
      <div class="person-title">Founder and CEO</div>
      <div class="address">418 Harlow Bend<br>Alderwick, MN 48199</div>
      <ul class="contact-list">
        <li>
          <svg viewBox="0 0 12 12" aria-hidden="true"><path d="M1 4 Q6 0 11 4 L9.5 5.5 L8 4.5 L8 3.5 Q6 3 4 3.5 L4 4.5 L2.5 5.5 Z"/><rect x="2.5" y="6" width="7" height="5" rx="1"/></svg>
          555 214-3086
        </li>
        <li>
          <svg viewBox="0 0 12 12" aria-hidden="true"><path d="M2.5 1 L4.5 1 L5.2 3.6 L4 4.6 Q5 7 7.4 8 L8.4 6.8 L11 7.5 L11 9.5 Q10.5 11 9 11 Q2 10 1 3 Q1 1.5 2.5 1 Z"/></svg>
          555 214-7720
        </li>
        <li>
          <svg viewBox="0 0 12 12" aria-hidden="true"><path d="M0.5 2.5 H11.5 V9.5 H0.5 Z M1.2 3 L6 6.6 L10.8 3" stroke="#fff" stroke-width="0.8"/></svg>
          DaneCorwell@volbreyinc.example
        </li>
        <li>
          <svg viewBox="0 0 12 12" aria-hidden="true"><circle cx="6" cy="6" r="5.5"/><path d="M0.5 6 H11.5 M6 0.5 V11.5 M6 0.5 Q2.5 6 6 11.5 M6 0.5 Q9.5 6 6 11.5" stroke="#fff" stroke-width="0.7" fill="none"/></svg>
          www.volbreyinc.example
        </li>
      </ul>
    </div>
  </section>

</body>
</html>
```